Local fast-growing company in the service sector

We are looking for a modern business card design, which should also appear on our letterheads

Target Market(s)

Private and industrial sectors

Contact Information for Business Card

Vorname Name
Kellberger Str. 18
71409 Lindenau
Tel.: 07146-839214-0
Name@agentur-kvtl.de

Colors
9d9d9d
919191
aaaaaa

Requirements
Must have
• The logo (file) in silver

```html
<!DOCTYPE html>
<html lang="de">
<head>
<meta charset="utf-8">
<title>KVTL Visitenkarte</title>
<link rel="stylesheet" href="https://fonts.googleapis.com/css2?family=Mulish:wght@400;700;800&display=swap">
<style>
  :root {
    --page-bg: #e6e6e6;
    --card-bg: #f4f4f4;
    --card-edge: #d2d2d2;
    --silver-dark: #5f5f5f;
    --silver: #919191;
    --silver-mid: #9d9d9d;
    --silver-light: #aaaaaa;
    --band: #6c6c6c;
    --band-text: #f2f2f2;
    --band-text-soft: #e2e2e2;
  }
  * { margin: 0; padding: 0; box-sizing: border-box; }
  html, body {
    width: 1200px;
    height: 969px;
    overflow: hidden;
    background: var(--page-bg);
    font-family: "Mulish", Arial, sans-serif;
  }
  .business-card {
    position: absolute;
    left: 165px;
    top: 237px;
    width: 870px;
    height: 495px;
    border-radius: 22px;
    background: var(--card-bg);
    border: 1px solid var(--card-edge);
    overflow: hidden;
    box-shadow: 0 10px 30px rgba(0,0,0,0.12);
  }
  .brand {
    position: absolute;
    left: 70px;
    top: 88px;
    display: flex;
    align-items: center;
    gap: 24px;
  }
  .brand-mark {
    width: 72px;
    height: 72px;
    background: var(--silver);
  }
  .brand-name {
    font-weight: 800;
    font-size: 92px;
    line-height: 1;
    letter-spacing: 2px;
    color: var(--silver-dark);
  }
  .info-band {
    position: absolute;
    left: 0;
    top: 252px;
    width: 870px;
    height: 188px;
  }
  .contact-person {
    position: absolute;
    left: 68px;
    top: 302px;
    color: var(--band-text-soft);
  }
  .person-name {
    font-size: 24px;
    font-weight: 700;
    color: var(--band-text);
    margin-bottom: 6px;
  }
  .address-line {
    font-size: 20px;
    line-height: 28px;
  }
  .band-divider {
    position: absolute;
    left: 275px;
    top: 305px;
    width: 2px;
    height: 84px;
    background: var(--silver-light);
  }
  .contact-list {
    position: absolute;
    left: 318px;
    top: 303px;
    list-style: none;
    color: var(--band-text-soft);
  }
  .contact-list li {
    display: flex;
    align-items: center;
    gap: 12px;
    font-size: 20px;
    line-height: 28px;
  }
  .contact-icon {
    width: 16px;
    height: 16px;
    flex: none;
  }
</style>
</head>
<body>
  <article class="business-card">
    <header class="brand">
      <span class="brand-mark"></span>
      <span class="brand-name">KVTL</span>
    </header>

    <svg class="info-band" viewBox="0 0 870 188" aria-hidden="true">
      <polygon points="0,0 700,0 700,130 870,130 870,188 0,188" fill="var(--band)" opacity="0.92"/>
    </svg>

    <div class="contact-person">
      <p class="person-name">Vorname Name</p>
      <p class="address-line">Kellberger Str. 18</p>
      <p class="address-line">71409 Lindenau</p>
    </div>

    <span class="band-divider"></span>

    <ul class="contact-list">
      <li>
        <svg class="contact-icon" viewBox="0 0 16 16" aria-hidden="true">
          <path d="M3 1.5l3 .5 1 3.2-1.8 1.3a9 9 0 0 0 4.3 4.3l1.3-1.8 3.2 1 .5 3-2 1.5C6.6 14 2 9.4 1.5 3.5z" fill="#e2e2e2"/>
        </svg>
        <span>07146-839214-0</span>
      </li>
      <li>
        <svg class="contact-icon" viewBox="0 0 16 16" aria-hidden="true">
          <rect x="1" y="3" width="14" height="10" rx="1" fill="#e2e2e2"/>
          <path d="M1.5 3.5L8 9l6.5-5.5" fill="none" stroke="#6c6c6c" stroke-width="1.3"/>
        </svg>
        <span>Name@agentur-kvtl.de</span>
      </li>
      <li>
        <svg class="contact-icon" viewBox="0 0 16 16" aria-hidden="true">
          <circle cx="8" cy="8" r="7" fill="#e2e2e2"/>
          <ellipse cx="8" cy="8" rx="3" ry="7" fill="none" stroke="#6c6c6c" stroke-width="1.1"/>
          <line x1="1" y1="8" x2="15" y2="8" stroke="#6c6c6c" stroke-width="1.1"/>
        </svg>
        <span>www.agentur-kvtl.de</span>
      </li>
    </ul>
  </article>
</body>
</html>
```